Folded A4 flyer for design&construction company

Folded A4 flyer needed. Keywords: elegant, stylish
our website www.dorvika.ae

Industry/Entity Type

Construction

```html
<!DOCTYPE html>
<html lang="en">
<head>
<meta charset="utf-8">
<title>Dorvika – Design &amp; Construction Flyer</title>
<link rel="stylesheet" href="https://fonts.googleapis.com/css2?family=Source+Sans+3:wght@300;400;600;700&family=Kaushan+Script&display=swap">
<style>
  :root {
    --stage: #a4a4a2;
    --slate: #4b4b50;
    --slate-dark: #3e3e43;
    --slate-light: #5a5a60;
    --gold: #b8922e;
    --gold-light: #e2b94a;
    --gold-deep: #7a6528;
    --white: #ffffff;
    --text-soft: #e6e6e8;
    --ink: #2b2b2b;
  }
  * { margin: 0; padding: 0; box-sizing: border-box; }
  html, body { width: 1200px; height: 789px; overflow: hidden; }
  body {
    background: var(--stage);
    font-family: "Source Sans 3", "Helvetica Neue", Arial, sans-serif;
    color: var(--white);
  }
  .spread {
    position: absolute;
    left: 105px; top: 44px;
    width: 990px; height: 700px;
    display: flex;
  }
  .page {
    position: relative;
    width: 495px; height: 700px;
    background: linear-gradient(180deg, var(--slate-light) 0%, var(--slate) 45%, var(--slate-dark) 100%);
    overflow: hidden;
  }
  .brand-name {
    font-weight: 300;
    color: var(--white);
    letter-spacing: 2px;
    text-align: center;
    line-height: 1;
  }

  /* back cover */
  .back .brand-name { position: absolute; top: 62px; width: 100%; font-size: 46px; }
  .back .about {
    position: absolute; top: 150px; left: 70px; right: 70px;
    font-size: 13.5px; line-height: 1.38; text-align: justify;
    text-align-last: center; color: var(--text-soft);
  }
  .back .ornament-area {
    position: absolute; top: 300px; left: 150px;
    width: 195px; height: 110px; border-radius: 55px;
    background: radial-gradient(ellipse at center, #6a6a71 0%, var(--slate) 75%);
  }
  .quote-badge {
    position: absolute; top: 462px; left: 62px;
    width: 118px; height: 118px; border-radius: 50%;
    background: radial-gradient(circle, var(--gold-light) 0%, #d9a830 70%, var(--gold) 100%);
    color: var(--ink); text-align: center;
    display: flex; flex-direction: column; justify-content: center;
    transform: rotate(-20deg);
    font-weight: 700; line-height: 1;
  }
  .quote-badge .small { font-size: 13px; font-weight: 600; }
  .quote-badge .big { font-size: 22px; }
  .contact {
    position: absolute; top: 470px; left: 210px; width: 240px;
    text-align: center;
  }
  .contact .phone { font-size: 26px; font-weight: 400; }
  .contact .or {
    display: inline-block; margin: 6px 0;
    background: var(--gold-deep); border-radius: 12px;
    padding: 0 12px; font-size: 18px; line-height: 24px;
  }
  .contact .email { font-size: 17px; }
  .web-band {
    position: absolute; left: 0; right: 0; height: 34px;
    background: linear-gradient(90deg, rgba(184,146,46,0) 0%, var(--gold) 25%, var(--gold) 75%, rgba(184,146,46,0) 100%);
    text-align: center; font-weight: 600; font-size: 17px; letter-spacing: 1px;
    line-height: 34px;
  }
  .back .web-band { top: 590px; }
  .address {
    position: absolute; top: 652px; width: 100%;
    text-align: center; font-size: 13.5px; color: var(--text-soft);
  }

  /* front cover */
  .front .brand-name { position: absolute; top: 92px; width: 100%; font-size: 70px; }
  .front .photo {
    position: absolute; top: 205px; left: 0; right: 0; height: 300px;
    background: linear-gradient(160deg, #d9d3c6 0%, #e0a72e 35%, #c98f2a 60%, #a56e22 100%);
  }
  .front .quote {
    position: absolute; top: 462px; width: 100%;
    text-align: center; font-family: "Kaushan Script", cursive;
    font-size: 19px; color: var(--white);
  }
  .front .web-band { top: 575px; }
</style>
</head>
<body>
  <main class="spread">
    <section class="page back">
      <h2 class="brand-name">DORVIKA</h2>
      <p class="about">We believe in quality beginnings and flawless finishes. We are a team of creative designers and constructors with years of experience and expertise in providing complete interior design and construction services. Our unique designing prowess is complemented by our unflinching commitment to quality construction. Our team specializes in classic and contemporary high quality construction in Dubai for commercial and residential projects.</p>
      <div class="ornament-area" role="img" aria-label="Decorative scroll ornament"></div>
      <div class="quote-badge">
        <span class="small">GET A</span>
        <span class="big">FREE<br>QUOTE</span>
        <span class="small">TODAY</span>
      </div>
      <div class="contact">
        <div class="phone">800-DORVIKA</div>
        <div class="or">or</div>
        <div class="email">CONTACT@DORVIKA.AE</div>
      </div>
      <div class="web-band">WWW.DORVIKA.AE</div>
      <p class="address">Dorvika LLC, Marlow Tower, Office 802, Harbour Quarter, Dubai</p>
    </section>
    <section class="page front">
      <h1 class="brand-name">DORVIKA</h1>
      <div class="photo" role="img" aria-label="Photo of a modern interior with curved yellow ceiling, spiral staircase and golden parquet floor"></div>
      <p class="quote">Quality is not an act, it is a habit - Theron Vale</p>
      <div class="web-band">WWW.DORVIKA.AE</div>
    </section>
  </main>
</body>
</html>
```